Im want a website LIKE VRX's and FleetHollow.com's with product payment options like Trenzo's

I need a website LIKE VRX with a header made EXACTLY LIKE THAT OF FLEETHOLLOWS .

The front page photo should be like that of FLEETHOLLOW's webpage as well.

The name of the website will be called "M.K. (Caldera Key)".

We will be targeting ALL MARKETS in a small town in central Panama and charging businesses "listing fees" like a phone book does but also providing informational blogs, news, and other interesting activities.

THIS IS A MULTI PAGE WEBSITE

THIS IS WHERE VRX's website meets Brivelle/FleetHollow.

Once the layout is built I will tweak and modify, add information, and upload items for sale.

Here is a list of specific categories that should be listed out above the front page header image/search bar

-- Home -- News -- Travel -- Activities -- Shop & Dine -- Store -- More... --

These categories should be spread across the bottom of the page in three sections:

WHATS SO GREAT ABOUT (Caldera Key),
HAND PICKED TOURS
ACTIVITIES etc.

Also lets use www.Trenzo.example 's
"HOT DESTINATIONS"
"BEAT THE BEST PRICES IN BOQUETE"
"OCTOBERS INSIDER PICKS"
"TOP DESTINATIONS"
and spread them in four sections side-by-side near the bottom of the page.

Overall I would like to see the finished product to be something LIKE VRX's and FleetHollows.

WE NEED ONLINE PAYMENT OPTIONS LIKE BRIVELLE'S WEBSITE HAS

This will be a desktop website but should be very mobile friendly as well.

-rodmund

P.S. Good luck!

If it isn't already too late to change the website name, the name of the website should be "Caldera Key". Added Friday, October 9, 2015

What do you guys think the budget should be to win this? Added Saturday, October 10, 2015

www.palmorra.example is the most amazing simple site. Whoever can make me a replica with my specifications will win immediately!!!! Added Sunday, October 18, 2015

OMG www.palmorra.example is the bomb!So simple and elegant. Whoever can make me an EXACT REPLICA OF WWW.PALMORRA.EXAMPLE as my site with the specifications mentioned in my brief will take home the $825.00 immediately! Good luck amigos! Added Sunday, October 18, 2015

Does anybody know how to add recurring monthly billing options on this website? Added Sunday, October 18, 2015

ALL MARKETS

Product

Coded - Design and coding required

5+ page

• Coinvey payment options.
• I must be able to add and remove photos/text and video from the HTML files in the page.
• Be creative my friends, and may the odds be forever in your favor!
• I added some photos of a good layout for our page below.

```html
<!DOCTYPE html>
<html lang="en">
<head>
<meta charset="utf-8">
<title>Caldera Key — Travel</title>
<link rel="stylesheet" href="https://fonts.googleapis.com/css2?family=Roboto:wght@100;300;400;500;700&family=Lobster&display=swap">
<style>
:root{
  --ink:#2b2b2b;
  --muted:#8a8a8a;
  --line:#e3e3e3;
  --white:#ffffff;
  --topbar:rgba(20,24,30,.85);
  --dark:#1f2327;
  --hero-a:#3e6f8e;
  --hero-b:#8aa7b5;
  --hero-c:#2f4a5c;
}
*{box-sizing:border-box;margin:0;padding:0}
html,body{width:1200px;height:3672px;overflow:hidden}
body{position:relative;background:var(--white);font-family:"Roboto",Arial,sans-serif;color:var(--ink)}
.abs{position:absolute}
.btn{display:inline-block;background:var(--white);color:var(--ink);border:1px solid var(--line);border-radius:24px;font-size:13px;font-weight:500;letter-spacing:1px;padding:12px 30px;text-transform:uppercase;white-space:nowrap}
.btn-outline{background:transparent;border-color:#cfcfcf}

/* hero */
.hero{left:0;top:0;width:1200px;height:900px;overflow:hidden}
.hero-photo{position:absolute;inset:0;background:linear-gradient(180deg,var(--hero-b) 0%,var(--hero-a) 45%,var(--hero-c) 100%)}
.topbar{position:absolute;left:0;top:0;width:1200px;height:48px;background:var(--topbar);display:flex;align-items:center;padding:0 48px;font-size:13px;color:#ddd}
.topbar .links{display:flex;gap:40px}
.topbar .account{margin-left:auto;margin-right:40px}
.topbar .search{width:230px;height:24px;border-bottom:1px solid #777;margin-right:40px}
.logo{position:absolute;left:0;width:1200px;top:66px;text-align:center;color:var(--white);font-size:44px;font-weight:500;letter-spacing:4px;text-transform:uppercase}
.nav{position:absolute;top:150px;left:0;width:1200px;display:flex;justify-content:center;gap:8px}
.nav a{color:var(--white);font-size:17px;padding:10px 26px;border-radius:22px;text-decoration:none;white-space:nowrap}
.nav a.active{background:var(--white);color:var(--ink)}
.hero-title{position:absolute;top:300px;width:1200px;text-align:center;font-family:"Lobster",cursive;font-size:150px;line-height:190px;font-weight:400;color:var(--white)}
.hero-copy{position:absolute;top:500px;left:340px;width:520px;text-align:center;color:var(--white);font-size:13px;line-height:20px}
.hero-price{position:absolute;top:566px;width:1200px;text-align:center;color:var(--white);font-size:40px;font-weight:500}
.hero-meta{position:absolute;top:628px;width:1200px;text-align:center;color:var(--white);font-size:13px;line-height:20px;letter-spacing:1px}
.hero .btn{position:absolute;top:712px;left:540px}
.dots{position:absolute;top:850px;width:1200px;display:flex;justify-content:center;gap:8px}
.dots i{width:8px;height:8px;border-radius:50%;background:rgba(255,255,255,.5)}
.dots i:first-child{background:var(--white)}

/* phone */
.callbar{left:0;top:924px;width:1200px;display:flex;justify-content:center;align-items:center;gap:16px;color:var(--muted);font-size:15px}
.callbar strong{font-size:46px;color:var(--ink);font-weight:500}

/* cards */
.card{top:1032px;width:352px;height:408px;border:1px solid var(--line);text-align:center}
.card .ph{height:220px;display:flex;align-items:center;justify-content:center;font-family:"Lobster",cursive;color:var(--white);font-size:46px;line-height:50px}
.card p{font-size:13px;color:var(--muted);line-height:20px;padding:28px 30px 0}
.card .more{position:absolute;bottom:30px;left:0;width:100%;font-size:12px;font-weight:500;letter-spacing:1px}
.card .more:before{content:"";display:block;width:100px;height:1px;background:var(--line);margin:0 auto 12px}

/* banner */
.banner{left:48px;top:1480px;width:1104px;height:332px;background:linear-gradient(180deg,#7fb3d4 0%,#3c8bbd 55%,#c8b796 100%);text-align:center;color:var(--white)}
.banner h2{margin-top:70px;font-size:84px;font-weight:300;letter-spacing:8px}
.banner h3{font-size:36px;font-weight:300;letter-spacing:8px;margin-top:4px}
.banner .btn{margin-top:30px}

/* products */
.section-title{left:0;width:1200px;text-align:center;font-size:32px;font-weight:400;letter-spacing:4px;text-transform:uppercase}
.product{top:1940px;width:258px;text-align:center}
.product .ph{height:250px;position:relative;overflow:hidden}
.product .name{margin-top:20px;font-size:13px;color:var(--muted)}
.product .price{margin-top:10px;font-size:22px;font-weight:500}
.product .price s{font-size:18px;color:var(--muted);font-weight:400;margin-left:8px}
.product .stars{margin-top:8px;font-size:15px;letter-spacing:3px}
.product .tools{margin-top:18px;display:flex;justify-content:space-between;padding:0 16px}
.sale{position:absolute;top:0;right:0;width:0;height:0;border-top:70px solid var(--dark);border-left:70px solid transparent}
.sale b{position:absolute;top:-58px;right:6px;color:var(--white);font-size:11px;transform:rotate(45deg)}

/* insurance */
.insurance{left:0;top:2440px;width:1200px;text-align:center}
.insurance h2{font-size:92px;font-weight:300;letter-spacing:10px}
.insurance h3{font-size:38px;font-weight:300;letter-spacing:10px;margin-top:6px}
.insurance hr{border:0;height:1px;background:var(--line);width:480px;margin:22px auto}
.insurance .btn{padding:10px 28px}

/* dark features */
.features{left:0;top:2712px;width:1200px;height:468px;background:linear-gradient(180deg,#3a4650 0%,#1f2327 60%,#2c3a44 100%);display:flex;justify-content:center;gap:60px;color:var(--white)}
.feature{width:300px;text-align:center;padding-top:80px}
.feature h4{margin-top:18px;font-size:36px;font-weight:300;letter-spacing:3px;text-transform:uppercase;white-space:nowrap}
.feature p{margin-top:24px;font-size:13px;line-height:20px;color:#ddd}
.feature .btn{margin-top:56px}

/* footer */
.footer{left:0;top:3220px;width:1200px;height:300px;border-top:1px solid var(--line)}
.fcol{position:absolute;top:36px;font-size:13px;line-height:26px}
.fcol h5{font-size:20px;font-weight:400;letter-spacing:3px;text-transform:uppercase;margin-bottom:16px}
.fcol p{color:var(--muted);line-height:20px}
.email{margin-top:22px;border-bottom:1px solid var(--line);padding-bottom:8px;color:var(--muted)}
.fcol .btn{margin-top:22px;padding:8px 26px;font-size:12px}
.fbox{width:310px;height:140px;border:1px solid var(--line)}
.fbox .head{height:64px;background:linear-gradient(90deg,#4d6d8d,#8aa4bd);color:var(--white);padding:14px;font-weight:500}
.fbox .row{display:flex;gap:6px;padding:12px}
.fbox .row i{width:36px;height:36px;background:#c8d2dc}
.copy{left:48px;top:3610px;font-size:12px;color:var(--muted)}
</style>
</head>
<body>

<header class="abs hero">
  <div class="hero-photo" role="img" aria-label="Photo of a canal city with gondolas and colourful buildings"></div>
  <div class="topbar">
    <div class="links"><span>Compare</span><span>Wishlist</span><span>Delivery</span><span>Help</span></div>
    <span class="account">My Account ▾</span>
    <div class="search"></div>
    <svg width="18" height="18" viewBox="0 0 24 24"><path d="M3 2h3l3 12h10l3-8H8" stroke="#ddd" stroke-width="2" fill="none"/><circle cx="9" cy="20" r="2" fill="#ddd"/><circle cx="18" cy="20" r="2" fill="#ddd"/></svg>
  </div>
  <div class="logo">Caldera Key</div>
  <nav class="nav">
    <a class="active">Home</a><a>News</a><a>Travel</a><a>Activities</a><a>Shop &amp; Dine</a><a>Store</a><a>More...</a>
  </nav>
  <h1 class="hero-title">Italy</h1>
  <p class="hero-copy">Praesent vestibulum aenean nonummy hendrerit mauris. Cum sociis natoque penatibus et magnis dis parturient montes, nascetur ridiculus mus. Nulla dui. Fusce feugiat malesuada odio.</p>
  <div class="hero-price">from $899</div>
  <div class="hero-meta">6-7 NIGHTS,<br>4 STAR HOTELS</div>
  <span class="btn">Click here</span>
  <div class="dots"><i></i><i></i><i></i></div>
</header>

<div class="abs callbar">
  <svg width="22" height="30" viewBox="0 0 22 30"><rect x="2" y="1" width="18" height="28" rx="3" fill="none" stroke="#999" stroke-width="2"/><circle cx="11" cy="24" r="1.6" fill="#999"/></svg>
  <span>Call us:</span><strong>800-555-0147</strong><span>Hours: 8am-17pm</span>
</div>

<article class="abs card" style="left:48px">
  <div class="ph" role="img" aria-label="Photo of friends on a cruise deck" style="background:linear-gradient(135deg,#9a6a48,#d8a77a)">Group<br>Cruises</div>
  <p>Praesent vestibulum aenean nonummy hendrerit mauris. Cum sociis natoque penatibus et magnis dis parturient montes, nascetur ridiculus mus.</p>
  <div class="more">READ MORE</div>
</article>
<article class="abs card" style="left:424px">
  <div class="ph" role="img" aria-label="Photo of a family at the seaside" style="background:linear-gradient(135deg,#6f8fa8,#c2a084)">Family<br>Travel</div>
  <p>Praesent vestibulum aenean nonummy hendrerit mauris. Cum sociis natoque penatibus et magnis dis parturient montes, nascetur ridiculus mus.</p>
  <div class="more">READ MORE</div>
</article>
<article class="abs card" style="left:800px">
  <div class="ph" role="img" aria-label="Photo of a couple on a tropical beach" style="background:linear-gradient(135deg,#4f9cbf,#d5c6a2)">Honeymoon<br>Package</div>
  <p>Praesent vestibulum aenean nonummy hendrerit mauris. Cum sociis natoque penatibus et magnis dis parturient montes, nascetur ridiculus mus.</p>
  <div class="more">READ MORE</div>
</article>

<section class="abs banner" role="img" aria-label="Photo of a beach with umbrellas and sun loungers by the sea">
  <h2>HOT SUMMER OFFERS</h2>
  <h3>MORE THAN 10 NEW DESTINATIONS</h3>
  <span class="btn">Click here</span>
</section>

<h2 class="abs section-title" style="top:1860px">Featured products:</h2>

<div class="abs product" style="left:48px">
  <div class="ph" role="img" aria-label="Photo of a golden temple in Thailand" style="background:linear-gradient(180deg,#6fa8d6,#b98a3e 60%,#4f7d3a)"></div>
  <div class="name">Hot Destinations</div><div class="price">$95.00</div><div class="stars">★★★★★</div>
  <div class="tools"><span>🛒︎ ⇄</span><span>♥</span></div>
</div>
<div class="abs product" style="left:330px">
  <div class="ph" role="img" aria-label="Photo of a colourful mosaic park" style="background:linear-gradient(180deg,#7ab0d8,#b8825a 60%,#7a6a4a)"><div class="sale"><b>Sale</b></div></div>
  <div class="name">Beat the Best Prices</div><div class="price">$70.00<s>$76.00</s></div><div class="stars">★★★★★</div>
  <div class="tools"><span>🛒︎ ⇄</span><span>♥</span></div>
</div>
<div class="abs product" style="left:612px">
  <div class="ph" role="img" aria-label="Photo of an old town church in autumn" style="background:linear-gradient(180deg,#8fb9dc,#c9a06a 55%,#8a5a30)"></div>
  <div class="name">October's Insider Picks</div><div class="price">$100.00</div><div class="stars">★★★★★</div>
  <div class="tools"><span>🛒︎ ⇄</span><span>♥</span></div>
</div>
<div class="abs product" style="left:894px">
  <div class="ph" role="img" aria-label="Photo of a snowy mountain village" style="background:linear-gradient(180deg,#a9c6df,#e8eef3 55%,#7c6a5a)"></div>
  <div class="name">Top Destinations</div><div class="price">$120.00</div><div class="stars">★★★★★</div>
  <div class="tools"><span>🛒︎ ⇄</span><span>♥</span></div>
</div>

<section class="abs insurance">
  <h2>TRAVEL INSURANCE</h2>
  <h3>SIMPLE &amp; FLEXIBLE.</h3>
  <hr>
  <span class="btn btn-outline">Click here</span>
</section>

<section class="abs features" role="img" aria-label="Dark photo of a waterfront promenade with palm trees">
  <div class="feature">
    <svg width="40" height="40" viewBox="0 0 40 40" fill="#fff"><rect x="8" y="6" width="24" height="30"/><rect x="13" y="11" width="4" height="4" fill="#333"/><rect x="23" y="11" width="4" height="4" fill="#333"/><rect x="13" y="19" width="4" height="4" fill="#333"/><rect x="23" y="19" width="4" height="4" fill="#333"/><rect x="17" y="28" width="6" height="8" fill="#333"/></svg>
    <h4>Why Here</h4>
    <p>Praesent vestibulum molestie lacus. Aenean nonummy hendrerit mauris. Phasellus porta. Fusce suscipit varius mi. Cum sociis natoque penatibus et magnis.</p>
    <span class="btn">Click here</span>
  </div>
  <div class="feature">
    <svg width="40" height="40" viewBox="0 0 40 40" fill="#fff"><path d="M20 2c2 0 3 2 3 4v10l14 8v4l-14-4v8l4 3v3l-7-2-7 2v-3l4-3v-8L3 28v-4l14-8V6c0-2 1-4 3-4z"/></svg>
    <h4>Top Tours</h4>
    <p>Praesent vestibulum molestie lacus. Aenean nonummy hendrerit mauris. Phasellus porta. Fusce suscipit varius mi. Cum sociis natoque penatibus et magnis.</p>
    <span class="btn">Click here</span>
  </div>
  <div class="feature">
    <svg width="44" height="40" viewBox="0 0 44 40" fill="#fff"><path d="M8 18l5-10h18l5 10h4v12h-4v4h-6v-4H14v4H8v-4H4V18z"/><circle cx="12" cy="24" r="2.5" fill="#333"/><circle cx="32" cy="24" r="2.5" fill="#333"/></svg>
    <h4>Activities</h4>
    <p>Praesent vestibulum molestie lacus. Aenean nonummy hendrerit mauris. Phasellus porta. Fusce suscipit varius mi. Cum sociis natoque penatibus et magnis.</p>
    <span class="btn">Click here</span>
  </div>
</section>

<footer class="abs footer">
  <div class="fcol" style="left:68px;top:68px">News<br>Travel<br>Activities<br>Shop &amp; Dine<br>Store</div>
  <div class="fcol" style="left:250px;top:42px">Compare<br>Wishlist<br>Delivery<br>Help</div>
  <div class="fcol" style="left:448px;width:340px">
    <h5>Newsletter:</h5>
    <p>Enter your email address to subscribe and receive notifications of new tours by email.</p>
    <div class="email">Enter your email here</div>
    <span class="btn btn-outline">Subscribe</span>
  </div>
  <div class="fcol" style="left:840px">
    <h5>Friendwall:</h5>
    <div class="fbox">
      <div class="head">Caldera Key</div>
      <div class="row"><i></i><i></i><i></i><i></i><i></i><i></i></div>
    </div>
  </div>
</footer>

<div class="abs copy">Caldera Key is proudly powered by our team. Privacy Policy</div>

</body>
</html>
```